Cat-products company needs smart, yet endearing, business card

We need a business card design for a new, but up-and-running, business based in Honolulu, Hawaii. The business is Purrnest Nook Co. Our first product is the most environmentally-friendly cat grass kit ever seen on the planet. Future products, currently in the R&D phase, will include a variety of exciting cat scratchers. We also do consulting work to help apartment-dwellers make their home more cat-friendly and, in the future, plan on doing full, custom installs of structure to create high walkways for cats.

Target Market(s)

Middle-aged, apartment-dwelling, middle-class workers who own 1 or more cats and who dote on them.

Industry/Entity Type

Pet Care

Contact Information for Business Card

A striking, professional, yet warm and friendly design is what we're after.

Font styles to use
Serif
Sans Serif
Other font styles liked:
• Comfortaa

Colors

Designer to choose colors to be used in the design.

Requirements
Must have
• The company logo: (see attachment)
• The company name: Purrnest Nook Co
• The web address: www.purrnestnookco.com
• Email: support@purrnestnookco.com
• Phone: +1 (808) 571 6023
• Update (Fri Jun 30 3017 7:45pm Hawaii Time) I would like, is possible, uploaded picture of the cat grass kit on the back of the card with some text along the lines of: Purrnest Nook Co - Maker Of The Leafiest Feline Sprout Set Yet
Nice to have
• A cat picture, cartoon, real or silhouette that illustrates cats in action and/or relaxing; ie using the apartment space to live, play and relax in and being well-contented.
• Most of the website is done in the font: Comfortaa. It might be nice to continue using this for brand consistency.
Should not have
• Hard-to-read fonts.

```html
<!DOCTYPE html>
<html lang="en">
<head>
<meta charset="utf-8">
<title>Purrnest Nook Co — Business Card</title>
<link rel="stylesheet" href="https://fonts.googleapis.com/css2?family=Comfortaa:wght@400;600;700&display=swap">
<style>
  :root {
    --stage: #232323;
    --card: #ffffff;
    --brand-brown: #5a3a34;
    --brand-amber: #f5ac1c;
    --mark-grey: #dcdcdc;
    --ink: #3a2a26;
    --ink-soft: #5c5c5c;
  }
  * { box-sizing: border-box; margin: 0; padding: 0; }
  html, body {
    width: 1200px;
    height: 1000px;
    overflow: hidden;
    background: var(--stage);
    font-family: "Comfortaa", sans-serif;
  }
  .stage { position: relative; width: 1200px; height: 1000px; }

  .card {
    position: absolute;
    width: 600px;
    height: 340px;
    background: var(--card);
    border-radius: 26px;
    overflow: hidden;
    box-shadow: 0 14px 30px rgba(0,0,0,.45);
  }
  .card--back { left: 110px; top: 110px; }
  .card--front { left: 490px; top: 550px; }

  /* Back: large faint company name as decoration */
  .back-name {
    position: absolute;
    right: 46px; top: 52px;
    width: 300px;
    font-size: 56px;
    line-height: 1.12;
    font-weight: 700;
    color: var(--mark-grey);
    text-align: right;
  }

  .signature {
    position: absolute;
    left: 30px; bottom: 28px;
    display: flex; align-items: center; gap: 10px;
  }
  .signature__dot {
    width: 20px; height: 20px;
    background: var(--brand-brown);
    border-radius: 4px;
  }
  .signature__name {
    font-weight: 700;
    font-size: 19px;
    color: var(--brand-amber);
  }

  /* Front */
  .brand-block {
    position: absolute;
    right: 44px; top: 44px;
    width: 210px; height: 210px;
    background: var(--brand-brown);
    border-radius: 12px;
  }
  .company-name {
    position: absolute;
    left: 32px; top: 62px;
    font-size: 26px;
    font-weight: 700;
    color: var(--brand-amber);
    letter-spacing: .3px;
  }

  .contact {
    position: absolute;
    left: 32px; top: 138px;
    color: var(--ink);
  }
  .contact__name {
    font-size: 22px;
    font-weight: 700;
    color: var(--brand-amber);
    line-height: 1.2;
  }
  .contact__role {
    font-size: 13px;
    color: var(--ink-soft);
    margin-top: 2px;
  }
  .contact__address {
    font-size: 12.5px;
    line-height: 1.45;
    margin-top: 10px;
  }
  .contact__lines {
    list-style: none;
    margin-top: 8px;
    font-size: 12.5px;
    line-height: 1.65;
  }
  .contact__lines li { display: flex; align-items: center; gap: 9px; }
  .contact__lines svg { width: 12px; height: 12px; flex: none; }
  .icon-fill { fill: var(--brand-amber); }
  .icon-stroke { fill: none; stroke: var(--brand-amber); stroke-width: 2.4; }
  .contact__web-domain { color: var(--brand-amber); }
</style>
</head>
<body>
<main class="stage">

  <section class="card card--back" aria-label="Card back">
    <p class="back-name" aria-hidden="true">Purrnest Nook Co</p>
    <div class="signature">
      <span class="signature__dot" aria-hidden="true"></span>
      <span class="signature__name">Purrnest Nook Co</span>
    </div>
  </section>

  <section class="card card--front" aria-label="Card front">
    <h1 class="company-name">Purrnest Nook Co</h1>
    <div class="brand-block" aria-hidden="true"></div>

    <div class="contact">
      <p class="contact__name">Leilani Kahale</p>
      <p class="contact__role">Director</p>
      <p class="contact__address">Your Street Address,<br>Country,1234</p>
      <ul class="contact__lines">
        <li>
          <svg viewBox="0 0 24 24" aria-hidden="true"><path class="icon-fill" d="M6.6 10.8a15.1 15.1 0 0 0 6.6 6.6l2.2-2.2a1 1 0 0 1 1-.25 11.4 11.4 0 0 0 3.6.57 1 1 0 0 1 1 1V20a1 1 0 0 1-1 1A17 17 0 0 1 3 4a1 1 0 0 1 1-1h3.5a1 1 0 0 1 1 1c0 1.25.2 2.45.57 3.57a1 1 0 0 1-.25 1z"/></svg>
          +1 (808) 571 6023
        </li>
        <li>
          <svg viewBox="0 0 24 24" aria-hidden="true"><rect class="icon-fill" x="2" y="5" width="20" height="14" rx="1"/><path d="M2.5 6l9.5 7.5L21.5 6" fill="none" stroke="#fff" stroke-width="2"/></svg>
          support@purrnestnookco.com
        </li>
        <li>
          <svg viewBox="0 0 24 24" aria-hidden="true"><circle class="icon-stroke" cx="12" cy="12" r="9.5"/><path class="icon-stroke" d="M2.5 12h19M12 2.5c3 3 3 16 0 19M12 2.5c-3 3-3 16 0 19"/></svg>
          <span>www.<span class="contact__web-domain">purrnestnookco</span>.com</span>
        </li>
      </ul>
    </div>
  </section>

</main>
</body>
</html>
```